Redesign of business card for Cedar Ridge Mechanical

We are looking for a new design for our business cards for Cedar Ridge Mechanical. We are a plumbing & HVAC construction company, operating on the West Coast of Canada and USA. Logo attached.
Industry/Entity Type
Construction - Plumbing & HVAC
Contact Information for Business Card
Name, address, phone numbers, email, website address
Look and feel
Each slider illustrates characteristics of the customer's brand and the style your logo design should communicate.

```html
<!DOCTYPE html>
<html lang="en">
<head>
<meta charset="utf-8">
<title>Cedar Ridge Mechanical – Business Card</title>
<link href="https://fonts.googleapis.com/css2?family=Montserrat:wght@400;500;700;800&display=swap" rel="stylesheet">
<style>
  :root {
    --page-bg: #1a1a1a;
    --card-black: #141414;
    --ink-white: #ffffff;
    --ink-grey: #9a9a9a;
    --stripe-grey: #8c8c8c;
    --swoosh-white: #f4f4f4;
  }
  * { box-sizing: border-box; margin: 0; padding: 0; }
  html, body {
    width: 1200px; height: 963px; overflow: hidden;
    background: var(--page-bg);
    font-family: "Montserrat", sans-serif;
  }
  .sheet {
    width: 1200px; height: 963px;
    display: flex; flex-direction: column; align-items: center; justify-content: center;
    gap: 50px;
  }
  .card {
    position: relative;
    width: 700px; height: 400px;
    background: var(--card-black);
    border-radius: 22px;
    overflow: hidden;
    box-shadow: 0 18px 40px rgba(0,0,0,.55);
    color: var(--ink-white);
  }
  .card-front .swoosh {
    position: absolute; left: 0; top: 0; width: 700px; height: 400px;
  }
  .brand {
    display: flex; align-items: center; gap: 12px;
    font-weight: 800; text-transform: uppercase; color: var(--ink-white);
    letter-spacing: .04em; line-height: 1.1;
  }
  .brand-square {
    flex: none; background: var(--ink-white);
  }
  .card-front .brand {
    position: absolute; left: 44px; top: 78px; width: 290px;
    font-size: 26px;
  }
  .card-front .brand-square { width: 30px; height: 30px; }
  .divider {
    position: absolute; left: 360px; top: 60px;
    width: 1px; height: 230px; background: var(--ink-white);
  }
  .contact {
    position: absolute; left: 388px; top: 70px; width: 300px;
  }
  .person-name {
    font-size: 24px; font-weight: 800; letter-spacing: .03em; text-transform: uppercase;
  }
  .person-role {
    font-size: 17px; font-weight: 500; margin-top: 2px;
  }
  .address {
    font-size: 16px; font-weight: 500; margin-top: 16px; line-height: 1.3;
  }
  .contact-list {
    list-style: none; margin-top: 16px; font-size: 16px; font-weight: 500;
  }
  .contact-list li { display: flex; align-items: center; gap: 8px; line-height: 1.55; }
  .contact-list svg { width: 14px; height: 14px; flex: none; }
  .card-back {
    display: flex; align-items: center; justify-content: center;
  }
  .card-back .brand {
    font-size: 40px; width: 520px;
  }
  .card-back .brand-square { width: 46px; height: 46px; }
</style>
</head>
<body>
<main class="sheet">
  <section class="card card-front" aria-label="Business card front">
    <svg class="swoosh" viewBox="0 0 700 400" aria-hidden="true">
      <path d="M0 170 C 40 230, 200 300, 700 400 L 0 400 Z" fill="var(--swoosh-white)"/>
      <path d="M0 150 C 60 215, 260 300, 700 372 C 260 290, 50 225, 0 175 Z" fill="var(--stripe-grey)"/>
      <path d="M0 178 C 60 240, 260 320, 700 400 L 700 400 L 0 400 Z" fill="var(--swoosh-white)"/>
      <path d="M140 400 C 360 400, 560 380, 700 320 L 700 400 Z" fill="var(--card-black)"/>
    </svg>
    <div class="brand">
      <span class="brand-square"></span>
      <span>Cedar Ridge Mechanical</span>
    </div>
    <div class="divider"></div>
    <div class="contact">
      <p class="person-name">Daniel Brooks</p>
      <p class="person-role">Manager</p>
      <p class="address">Your address, city<br>state, ZIP 0000</p>
      <ul class="contact-list">
        <li>
          <svg viewBox="0 0 24 24"><path fill="var(--ink-white)" d="M6.6 10.8a15 15 0 0 0 6.6 6.6l2.2-2.2a1 1 0 0 1 1-.25 11.4 11.4 0 0 0 3.6.57 1 1 0 0 1 1 1V20a1 1 0 0 1-1 1A17 17 0 0 1 3 4a1 1 0 0 1 1-1h3.5a1 1 0 0 1 1 1c0 1.25.2 2.45.57 3.57a1 1 0 0 1-.25 1z"/></svg>
          604-555-0142
        </li>
        <li>
          <svg viewBox="0 0 24 24"><rect x="2" y="5" width="20" height="14" rx="2" fill="var(--ink-white)"/><path d="M3 6l9 7 9-7" stroke="var(--card-black)" stroke-width="2" fill="none"/></svg>
          info@cedarridgemech.com
        </li>
        <li>
          <svg viewBox="0 0 24 24"><circle cx="12" cy="12" r="10" fill="var(--ink-white)"/><path d="M2 12h20M12 2c3 3 3 17 0 20M12 2c-3 3-3 17 0 20" stroke="var(--card-black)" stroke-width="1.5" fill="none"/></svg>
          www.cedarridgemech.com
        </li>
      </ul>
    </div>
  </section>

  <section class="card card-back" aria-label="Business card back">
    <div class="brand">
      <span class="brand-square"></span>
      <span>Cedar Ridge Mechanical</span>
    </div>
  </section>
</main>
</body>
</html>
```